K7 Electrical Services Ltd Web design

I require a web site for my new electrical contracting company. We are customer service orientated. Offering high value electrical installations, design and maintenance. Focused on custom residential and commercial upgrading. Lighting design and application are paramount in our company's services. Industry leading product use and integration are always on the forefront with our customer client services. As well as energy efficiency.

Target Market(s)

Homebuilders, General Contractors, Property management companies, clients, individuals,

Industry/Entity Type

Electric Company

Coding

Coded - Design and coding required

Number of Pages Required

3 page

Requirements
Must have
• Classic, modern, edgy but not trendy . Appeals to the masse.
• 3 page
• home page
• about page
• gallery page
• ability to contact from the webiste
Nice to have
• open to all types of designs that are relative to the construction industry.
• Black, Grey, metallic ice blue and deep purple colours from the logo.
Should not have
• anything cheesy with cartoon light bulb images.

```html
<!DOCTYPE html>
<html lang="en">
<head>
<meta charset="utf-8">
<title>K7 Electrical Services Ltd</title>
<link href="https://fonts.googleapis.com/css2?family=Lato:wght@300;400;700;900&display=swap" rel="stylesheet">
<style>
:root{
  --purple:#5b2a8c;
  --purple-dark:#4a1f75;
  --ink:#333;
  --grey-text:#666;
  --light-grey:#f2f2f2;
  --footer:#2f2f2f;
  --white:#fff;
  --ice:#9fb4c4;
}
*{box-sizing:border-box;margin:0;padding:0}
html,body{width:1200px;height:2644px;overflow:hidden}
body{font-family:"Lato",sans-serif;color:var(--ink);background:var(--white);position:relative}
.site-header{position:absolute;top:0;left:0;width:1200px;height:120px;background:var(--white)}
.brand{position:absolute;left:64px;top:28px;display:flex;align-items:center;gap:14px}
.brand-dot{width:56px;height:56px;border-radius:50%;background:var(--purple)}
.brand-name{font-size:26px;font-weight:700;color:var(--purple);line-height:1.1;width:200px}
.call-now{position:absolute;right:78px;top:26px;font-size:17px;font-weight:700;color:#444}
.call-now span{font-weight:400}
.main-nav{position:absolute;right:78px;top:72px;display:flex;gap:36px}
.main-nav a{font-size:15px;text-decoration:none;color:#555;text-transform:uppercase;padding-bottom:8px}
.main-nav a.active{color:var(--purple);border-bottom:2px solid var(--purple)}
.hero{position:absolute;top:120px;left:0;width:1200px;height:610px;background:linear-gradient(120deg,#3d4854 0%,#6f7c88 40%,#b8c2ca 70%,#8a97a3 100%)}
.hero-title{position:absolute;top:206px;left:0;width:100%;text-align:center;color:var(--white);font-size:58px;font-weight:700;line-height:1.3}
.services{position:absolute;top:676px;left:76px;width:1048px;display:flex;justify-content:space-between}
.service-card{width:310px;height:336px;background:var(--white);border:1px solid #ddd;box-shadow:0 2px 8px rgba(0,0,0,.08);padding:40px 30px 0}
.service-icon{width:100px;height:100px;border-radius:50%;background:var(--purple);margin:0 auto 34px;display:flex;align-items:center;justify-content:center}
.service-card h3{color:var(--purple);font-size:22px;font-weight:400;margin-bottom:12px}
.service-card p{font-size:14px;line-height:1.6;color:var(--grey-text)}
.welcome{position:absolute;top:1082px;left:0;width:1200px;height:340px;background:var(--light-grey);text-align:center;padding-top:42px}
.welcome h2{color:var(--purple);font-size:44px;font-weight:700;margin-bottom:22px}
.welcome p{width:780px;margin:0 auto 16px;font-size:14px;line-height:1.7;color:var(--grey-text)}
.btn{display:inline-block;background:var(--purple);color:var(--white);font-size:16px;font-weight:700;letter-spacing:1px;padding:12px 30px;text-decoration:none}
.tools{position:absolute;top:1422px;left:0;width:1200px;height:210px;background:linear-gradient(180deg,#ffffff 0%,#e7e4ea 100%)}
.cta-band{position:absolute;top:1632px;left:0;width:1200px;height:138px;background:var(--purple);padding:36px 78px;color:var(--white)}
.cta-band h2{font-size:36px;font-weight:700}
.cta-band p{font-size:17px;margin-top:6px}
.cta-band .btn-light{position:absolute;right:78px;top:48px;background:var(--white);color:var(--ink);font-size:16px;font-weight:700;padding:12px 18px;text-decoration:none}
.gallery{position:absolute;top:1830px;left:0;width:1200px;text-align:center}
.gallery h2{color:var(--purple);font-size:44px;font-weight:700}
.gallery-row{position:absolute;top:92px;left:76px;width:1048px;display:flex;justify-content:space-between}
.gallery-item{width:244px;height:258px}
.g1{background:linear-gradient(160deg,#b9c7d4,#4d6a86)}
.g2{background:linear-gradient(160deg,#d6d8d4,#5c7a5c)}
.g3{background:linear-gradient(160deg,#e6d8c2,#8a6a4a)}
.g4{background:linear-gradient(160deg,#e8dcc6,#9a7e5e)}
.arrow{position:absolute;top:390px;width:52px;height:40px;background:var(--purple);display:flex;align-items:center;justify-content:center}
.arrow.prev{left:78px}.arrow.next{right:78px}
.site-footer{position:absolute;top:2400px;left:0;width:1200px;height:244px;background:var(--footer)}
.contact-bar{position:absolute;top:2328px;left:76px;width:1048px;height:152px;background:var(--purple);display:flex;align-items:center;padding:0 40px;gap:70px;color:var(--white)}
.contact-item{display:flex;align-items:center;gap:22px}
.contact-icon{width:62px;height:62px;border-radius:50%;border:2px solid rgba(255,255,255,.6);display:flex;align-items:center;justify-content:center}
.contact-item h4{font-size:22px;font-weight:700}
.contact-item p{font-size:14px;line-height:1.5;width:200px}
.footer-nav{position:absolute;top:2520px;left:78px;display:flex;gap:36px}
.footer-nav a{color:var(--white);font-size:15px;text-decoration:none}
.social{position:absolute;top:2510px;right:78px;display:flex;gap:14px}
.social span{width:40px;height:40px;border-radius:50%;background:var(--white)}
.copyright{position:absolute;top:2574px;left:78px;width:1044px;border-top:1px solid #555;padding-top:18px;text-align:center;color:#ccc;font-size:14px}
</style>
</head>
<body>
<header class="site-header">
  <div class="brand"><span class="brand-dot"></span><span class="brand-name">K7 Electrical Services</span></div>
  <div class="call-now">CALL NOW : <span>123 456 7890</span></div>
  <nav class="main-nav">
    <a class="active" href="#">Home</a><a href="#">About Us</a><a href="#">Gallery</a><a href="#">Contact Us</a>
  </nav>
</header>

<section class="hero" role="img" aria-label="Electrician working at an electrical distribution panel">
  <h1 class="hero-title">Lorem Ipsum is simply<br>dummy text .</h1>
</section>

<section class="services">
  <article class="service-card">
    <div class="service-icon"><svg width="46" height="46" viewBox="0 0 24 24" fill="none" stroke="#fff" stroke-width="2" stroke-linecap="round"><path d="M9 2v6M15 2v6M6 8h12v4a6 6 0 0 1-12 0z M12 18v4"/></svg></div>
    <h3>Electrical installations</h3>
    <p>Lorem Ipsum is simply dummy text of the printing and typesetting industry. Lorem Ipsum has been the industry's.</p>
  </article>
  <article class="service-card">
    <div class="service-icon"><svg width="46" height="46" viewBox="0 0 24 24" fill="none" stroke="#fff" stroke-width="2"><rect x="7" y="7" width="10" height="10"/><path d="M10 3v4M14 3v4M10 17v4M14 17v4M3 10h4M3 14h4M17 10h4M17 14h4"/></svg></div>
    <h3>Design</h3>
    <p>Lorem Ipsum is simply dummy text of the printing and typesetting industry. Lorem Ipsum has been the industry's.</p>
  </article>
  <article class="service-card">
    <div class="service-icon"><svg width="46" height="46" viewBox="0 0 24 24" fill="none" stroke="#fff" stroke-width="2" stroke-linecap="round"><path d="M4 20l9-9M14 4a4 4 0 0 0 6 6l-3-1-2-2z M4 4l6 6M4 4l2-1 1 2"/></svg></div>
    <h3>Maintenance</h3>
    <p>Lorem Ipsum is simply dummy text of the printing and typesetting industry. Lorem Ipsum has been the industry's.</p>
  </article>
</section>

<section class="welcome">
  <h2>Welcome to K7 Electrical Services</h2>
  <p>Lorem Ipsum is simply dummy text of the printing and typesetting industry. Lorem Ipsum has been the industry's standard dummy text ever since the 1500s, when an unknown printer took a galley of type and scrambled it to make a type specimen book. It has survived not only five centuries, but also the leap into electronic typesetting.</p>
  <p>Lorem Ipsum is simply dummy text of the printing and typesetting industry. Lorem Ipsum has been the industry's standard dummy text ever since the 1500s, when an unknown printer took a galley of type and scrambled.</p>
  <a class="btn" href="#">READ MORE</a>
</section>

<div class="tools" role="img" aria-label="Electrician tools: multimeter, screwdrivers, cables and pliers"></div>

<section class="cta-band">
  <h2>Have Any Housing Problems?</h2>
  <p>Our experts will solve them in no time.</p>
  <a class="btn-light" href="#">CONTACT US NOW</a>
</section>

<section class="gallery">
  <h2>Project Gallery</h2>
  <div class="gallery-row">
    <div class="gallery-item g1" role="img" aria-label="Commercial interior project with lighting"></div>
    <div class="gallery-item g2" role="img" aria-label="Industrial wiring installation"></div>
    <div class="gallery-item g3" role="img" aria-label="Residential kitchen lighting project"></div>
    <div class="gallery-item g4" role="img" aria-label="Classic interior with upgraded lighting"></div>
  </div>
  <div class="arrow prev"><svg width="22" height="16" viewBox="0 0 22 16" fill="none" stroke="#fff" stroke-width="2.5"><path d="M21 8H2M8 2L2 8l6 6"/></svg></div>
  <div class="arrow next"><svg width="22" height="16" viewBox="0 0 22 16" fill="none" stroke="#fff" stroke-width="2.5"><path d="M1 8h19M14 2l6 6-6 6"/></svg></div>
</section>

<footer class="site-footer"></footer>
<div class="contact-bar">
  <div class="contact-item">
    <div class="contact-icon"><svg width="26" height="26" viewBox="0 0 24 24" fill="none" stroke="#fff" stroke-width="2"><path d="M12 22s7-7 7-12a7 7 0 0 0-14 0c0 5 7 12 7 12z"/><circle cx="12" cy="10" r="2.5"/></svg></div>
    <div><h4>Address</h4><p>Lorem Ipsum is simply dummy text of the printing.</p></div>
  </div>
  <div class="contact-item">
    <div class="contact-icon"><svg width="26" height="26" viewBox="0 0 24 24" fill="none" stroke="#fff" stroke-width="2"><path d="M5 3h4l2 5-3 2a11 11 0 0 0 6 6l2-3 5 2v4a2 2 0 0 1-2 2A17 17 0 0 1 3 5a2 2 0 0 1 2-2z"/></svg></div>
    <div><h4>Phone</h4><p>123 456 7890</p></div>
  </div>
  <div class="contact-item">
    <div class="contact-icon"><svg width="26" height="26" viewBox="0 0 24 24" fill="none" stroke="#fff" stroke-width="2"><rect x="3" y="5" width="18" height="14"/><path d="M3 6l9 7 9-7"/></svg></div>
    <div><h4>Email</h4><p>info@k7electrical.com</p></div>
  </div>
</div>
<nav class="footer-nav"><a href="#">Home</a><a href="#">About Us</a><a href="#">Gallery</a><a href="#">Contact Us</a></nav>
<div class="social"><span></span><span></span><span></span></div>
<div class="copyright">©K7 ELECTRICAL - 2016. All Rights Reserved.</div>
</body>
</html>
```